New Business Card Design for Manufacturing

We are an engineering/manufacturing company that offers Advanced machining/assembly/engineering services, as well as innovative products for the heavy duty engine cooling markets.

We are looking to get a new business card designed that is clean and modern looking, but still fits the wide range of technical/skilled work we do.

- We hope to use this design as the base for other design work in new Presentations, web, and print work.

Industry/Entity Type

Engineering

Contact Information for Business Card

Our preferred color of blue is (RGB) 22/71/159 but can vary slightly from that color. Our content will be our Logo and full company name (Vantrell Forge Works, Inc.), company address, name, job title, phone number with extension, cell number, fax number, website, and email address on the cards.
We'd like the full company name next to the logo, but we are open to other interpretations of that layout.
Preferably, we would like the back side to be clean with just our logo, and the front to contain all of the contact information.

Colors
2f74b4
0355a3
85abd2

Requirements
Must have
• - Logo, company name, needed content - We are open to interpretation beyond that.
• - Standard size business card.
• - Horizontal orientation.
• - Enough space for lengthy names / job titles (for example, a job title could read "Directory of Human Resources" or "V.P. of Governmental Affairs"). We need this to look clean, whether the title be short (CEO) or long (as described above).

```html
<!DOCTYPE html>
<html lang="en">
<head>
<meta charset="utf-8">
<title>Vantrell Forge Works – Business Card</title>
<link href="https://fonts.googleapis.com/css2?family=Open+Sans:wght@400;600;700&display=swap" rel="stylesheet">
<style>
  :root {
    --backdrop: #3a3a3c;
    --card-black: #1c1c1e;
    --card-edge: #111112;
    --gloss-black: #2c2c2f;
    --steel: #8c9094;
    --steel-dark: #5d6165;
    --brand-blue: #0355a3;
    --brand-blue-mid: #2f74b4;
    --brand-blue-light: #1b86d6;
    --brand-sky: #85abd2;
    --ink-white: #ffffff;
    --ink-dark: #141416;
  }
  * { margin: 0; padding: 0; box-sizing: border-box; }
  html, body { width: 799px; height: 1200px; overflow: hidden; }
  body {
    background: var(--backdrop);
    font-family: "Open Sans", Arial, sans-serif;
    position: relative;
  }
  .card {
    position: absolute;
    left: 70px;
    width: 660px;
    height: 377px;
    background: var(--card-black);
    border-radius: 3px;
    box-shadow: 0 14px 30px rgba(0,0,0,.55);
    overflow: hidden;
  }
  .card--back { top: 90px; }
  .card--front { top: 700px; }

  /* back side */
  .brand-mark {
    position: absolute;
    left: 0; right: 0; top: 150px;
    display: flex; align-items: center; justify-content: center; gap: 14px;
  }
  .brand-mark__square {
    width: 34px; height: 34px;
    background: var(--gloss-black);
  }
  .brand-mark__name {
    font-weight: 700;
    font-size: 64px;
    letter-spacing: 2px;
    line-height: 1;
    color: var(--gloss-black);
    text-transform: uppercase;
  }

  /* front side */
  .front-logo {
    position: absolute;
    right: 150px; top: 34px;
    display: flex; align-items: center; gap: 10px;
  }
  .front-logo__square { width: 22px; height: 22px; background: var(--brand-blue-light); }
  .front-logo__name {
    font-weight: 700; font-size: 42px; line-height: 1;
    letter-spacing: 1px; text-transform: uppercase;
    color: var(--brand-blue-light);
  }
  .front-logo__tagline {
    position: absolute; right: 150px; top: 86px;
    font-weight: 700; font-size: 11px; letter-spacing: 2px;
    color: var(--steel); text-transform: uppercase;
  }
  .company-band {
    position: absolute; left: 0; right: 0; top: 112px; height: 34px;
    background: linear-gradient(90deg, var(--steel-dark), var(--steel) 45%, var(--steel-dark));
    display: flex; align-items: center; justify-content: flex-end; padding-right: 92px;
  }
  .company-band__name {
    font-weight: 700; font-size: 17px; color: var(--ink-white);
  }
  .contact-band {
    position: absolute; left: 0; right: 0; top: 146px; height: 170px;
    background: linear-gradient(90deg, var(--brand-blue) 0%, var(--brand-blue-light) 50%, var(--brand-blue) 100%);
  }
  .person {
    position: absolute; left: 40px; top: 22px; width: 270px; text-align: right;
  }
  .person__name { font-weight: 600; font-size: 26px; color: var(--ink-white); line-height: 1.2; }
  .person__title { font-size: 14px; color: var(--ink-white); line-height: 1.3; margin-top: 4px; }
  .divider {
    position: absolute; left: 336px; top: 20px; width: 1.5px; height: 130px;
    background: var(--ink-white);
  }
  .contact-list {
    position: absolute; left: 356px; top: 22px; list-style: none;
  }
  .contact-list li {
    display: flex; align-items: center; gap: 10px;
    font-size: 15px; color: var(--ink-white); line-height: 25px;
  }
  .contact-list svg { width: 14px; height: 14px; flex: none; fill: var(--ink-white); }
  .address {
    position: absolute; left: 0; right: 0; top: 330px; text-align: center;
    font-size: 16px; color: var(--ink-white);
  }
</style>
</head>
<body>

<section class="card card--back" aria-label="Card back">
  <div class="brand-mark">
    <span class="brand-mark__square"></span>
    <span class="brand-mark__name">Vantrell</span>
  </div>
</section>

<section class="card card--front" aria-label="Card front">
  <div class="front-logo">
    <span class="front-logo__square"></span>
    <span class="front-logo__name">Vantrell</span>
  </div>
  <div class="front-logo__tagline">Built to Endure</div>

  <div class="company-band">
    <span class="company-band__name">Vantrell Forge Works, Inc.</span>
  </div>

  <div class="contact-band">
    <div class="person">
      <div class="person__name">Marlo Keane Addison</div>
      <div class="person__title">Managing Director / Admin<br>PhD Holder / Owner /<br>Technician / Developer / Producer</div>
    </div>
    <div class="divider"></div>
    <ul class="contact-list">
      <li><svg viewBox="0 0 16 16" aria-hidden="true"><path d="M3 1h3l1.5 4-2 1.3a9 9 0 0 0 4.2 4.2L11 8.5l4 1.5v3a2 2 0 0 1-2 2A12 12 0 0 1 1 3a2 2 0 0 1 2-2z"/></svg>555-0142-2200 (VFW)</li>
      <li><svg viewBox="0 0 16 16" aria-hidden="true"><path d="M4 1h7v4H4zM1 6h14v7h-3v2H4v-2H1zm4 5v3h6v-3z"/></svg>555-0187-3310</li>
      <li><svg viewBox="0 0 16 16" aria-hidden="true"><path d="M4 0h8a1 1 0 0 1 1 1v14a1 1 0 0 1-1 1H4a1 1 0 0 1-1-1V1a1 1 0 0 1 1-1zm1 2v10h6V2zm3 11a1 1 0 1 0 0 2 1 1 0 0 0 0-2z"/></svg>555-0163-4471</li>
      <li><svg viewBox="0 0 16 16" aria-hidden="true"><path d="M1 3h14v10H1zm1.5 1.2V5l5.5 4 5.5-4v-.8z"/></svg>mkaddison@vantrellforge.com</li>
      <li><svg viewBox="0 0 16 16" aria-hidden="true"><path d="M8 0a8 8 0 1 0 0 16A8 8 0 0 0 8 0zm0 1.5c1 0 2 1.7 2.4 4.5H5.6C6 3.2 7 1.5 8 1.5zM1.6 7H4.4a14 14 0 0 0 0 2H1.6a6.5 6.5 0 0 1 0-2zm4 0h4.8a13 13 0 0 1 0 2H5.6a13 13 0 0 1 0-2zm6 0h2.8a6.5 6.5 0 0 1 0 2h-2.8a14 14 0 0 0 0-2zM5.6 10h4.8c-.4 2.8-1.4 4.5-2.4 4.5S6 12.8 5.6 10z"/></svg>www.vantrellforge.com</li>
    </ul>
  </div>

  <div class="address">78 Millrace Rd., Granby Falls, US 40219</div>
</section>

</body>
</html>
```